Brimora - Nutritious Snacks and Desserts

We need a creative e-commerce website in which all features--buttons, background, etc.--convey our message: We sell delicious, nutritious snacks and desserts that most closely comply with the paleo diet guidelines. Our first product is Nuttaree®--raw, vegan, paleo chocolate balls that are made of dates, coconut, and cocoa. Our products are organic, raw, irresistible and nutritious. We have several versions of Nuttaree® in development, as well as mousse, ice cream, and crackers. Our mission is to purvey basic healthy foods. Our motto is, "Fuel for the Bold Trail-Walker(tm)."

Target Market(s)

Health-conscious professionals who tend to shop at health food stores. Our products also meet the requirements of a gluten-free diet; and they also don't contain refined sugar, so shoppers with gluten and possibly sugar issues are incidental customers.

Industry/Entity Type

Health Product

Coding

Number of Pages Required

5+ page

Colors

Designer to choose colors to be used in the design.

Requirements
Must have
• We need at least a home page, a products page, an about-us page, a contact page, and a shopping cart page. We would like to be able to add products on our own later. We should be able to handle some basic coding, especially if it's just a matter of copying and modifying product pages. We would also like the ability in the future to add blogging pages, allowing us to write articles about health food and healthy lifestyle, thus attracting web-traffic (SEO).
• Other features we would like to have:
• Product photo slider on the hopepage
• Back-to-top button at the bottom of the home page
• Make sure the site is mobile-compatible
• A search bar at the top of the homepage
• "Create an account" and "Previous orders"--allowing customers to see their previous orders and reorder what they purchased in the past.
Nice to have
• We would like to convey the paleo theme without actually stating it anywhere. We'll add text as necessary, according to the page layout; you can use ipsum lorem for purpose of demonstration.

```html
<!DOCTYPE html>
<html lang="en">
<head>
<meta charset="utf-8">
<title>Brimora – Nutritious Snacks and Desserts</title>
<link href="https://fonts.googleapis.com/css2?family=Kaushan+Script&family=Courgette&display=swap" rel="stylesheet">
<style>
:root{
  --lime:#86ab1c;
  --lime-dark:#6b9214;
  --leaf:#6c9c12;
  --forest:#3f7614;
  --meadow:#4b9a1e;
  --cocoa:#3b2320;
  --cocoa-mid:#5a2f2b;
  --cream:#fffbe6;
  --ink:#3a3a3a;
  --line:#e3e3e3;
  --white:#ffffff;
}
*{margin:0;padding:0;box-sizing:border-box}
html,body{width:1200px;height:3315px;overflow:hidden}
body{position:relative;background:var(--white);font-family:"Courgette",cursive;color:var(--ink)}
.script{font-family:"Kaushan Script",cursive}
.photo{position:absolute;border-radius:6px}

/* hero */
.hero{position:absolute;left:0;top:0;width:1200px;height:730px;overflow:hidden;
  background:radial-gradient(ellipse at 70% 60%,#9bbd2a 0%,var(--lime) 45%,var(--lime-dark) 100%)}
.nav a{position:absolute;top:34px;font-size:19px;color:#d8ec55;text-decoration:none}
.nav a.current{color:var(--cream);text-decoration:underline}
.cart-pill{position:absolute;left:935px;top:24px;width:186px;height:42px;border:2px solid #d8ec55;border-radius:22px;
  color:var(--cream);font-size:18px;padding:8px 0 0 22px}
.cart-dot{position:absolute;right:4px;top:3px;width:54px;height:32px;border-radius:16px;background:#7ab81e}
.brand{position:absolute;left:0;top:66px;width:1200px;text-align:center}
.brand-mark{width:76px;height:76px;border-radius:50%;border:3px solid #8a7f77;margin:0 auto 4px}
.brand-name{font-size:40px;color:#d9d2cc;letter-spacing:4px;line-height:1.2}
.hero-title{position:absolute;left:640px;top:345px;font-size:100px;color:#111;line-height:1;font-weight:400}
.hero-tag{position:absolute;left:642px;top:470px;width:520px;font-size:25px;color:#1b1b1b;line-height:1.35}
.btn-shop{position:absolute;left:641px;top:565px;width:234px;height:52px;border-radius:26px;background:var(--cocoa-mid);
  color:#e9d45f;font-size:23px;text-align:center;line-height:50px;border:2px solid #7a4a40}

/* welcome */
.welcome-title{position:absolute;left:0;top:840px;width:1200px;text-align:center;font-size:68px;color:var(--leaf);font-weight:400;line-height:1.2}
.welcome-title span{color:#7bb516}
.welcome-text{position:absolute;left:230px;top:944px;width:720px;text-align:center;font-size:16px;color:#8a8a8a;line-height:1.7}
.welcome-text p+p{margin-top:20px}
.watermark-ring{position:absolute;left:505px;top:800px;width:250px;height:250px;border-radius:50%;border:26px solid #f3f3f3}
.divider{position:absolute;left:77px;top:1187px;width:1046px;height:2px;background:#c9d29b}
.divider-dot{position:absolute;left:585px;top:1174px;width:30px;height:30px;border-radius:50%;background:var(--white);border:2px solid #c9d29b}
.divider-dot::after{content:"";position:absolute;left:6px;top:6px;width:14px;height:14px;border-radius:50%;background:#8fb52a}

/* cards */
.card{position:absolute;width:252px;height:388px;border:1px solid var(--line);background:var(--white);text-align:center}
.card.feature{border:2px solid #dedede;box-shadow:0 2px 8px rgba(0,0,0,.08);text-align:left;padding:34px 18px}
.feature h3{font-size:36px;color:var(--cocoa);font-weight:400;margin-bottom:22px}
.feature h3 span{color:#7bb516}
.feature p{font-size:14px;color:#9a9a9a;line-height:1.9}
.card-name{position:absolute;left:0;top:30px;width:100%;font-size:18px;color:#2a3a05}
.card-price{position:absolute;left:0;top:330px;width:100%;font-size:20px;color:#6b9c14}
.card-price b{color:#1e2a05;font-weight:400}
.card-note{position:absolute;left:20px;top:300px;width:212px;font-size:14px;color:#b7b7b7;line-height:1.5}
.card-name.low{top:262px}
.tools{position:absolute;left:38px;top:176px;display:flex;gap:22px}
.tool{width:44px;height:44px;border-radius:50%;border:2px solid #3a3a3a;background:rgba(255,255,255,.85);display:flex;align-items:center;justify-content:center}

/* testimonial */
.testimonial{position:absolute;left:0;top:1725px;width:1200px;height:343px;
  background:linear-gradient(180deg,var(--forest),#3a6d10 60%,#447c16)}
.testimonial h2{position:absolute;left:0;top:56px;width:1200px;text-align:center;font-size:64px;color:var(--white);font-weight:400;line-height:1.2}
.testimonial p{position:absolute;left:200px;top:160px;width:800px;text-align:center;font-size:15px;color:#8fbf4a;line-height:1.75}
.testimonial .who{position:absolute;left:0;top:258px;width:1200px;text-align:center;font-size:18px;color:var(--white)}
.quote{position:absolute;font-family:Georgia,serif;font-size:86px;color:#9fcb6a;line-height:1}

/* contact */
.contact{position:absolute;left:0;top:2588px;width:1200px;height:727px;overflow:hidden;
  background:radial-gradient(ellipse at 50% 40%,#55a522 0%,var(--meadow) 50%,#3f8a16 100%)}
.contact h2{position:absolute;left:0;width:1200px;text-align:center;font-size:62px;color:var(--white);font-weight:400;line-height:1}
.contact .lead{position:absolute;left:320px;top:158px;width:560px;text-align:center;font-size:17px;color:var(--white);line-height:1.55}
.ci{position:absolute;top:228px;width:58px;height:58px;border-radius:50%;background:var(--cocoa-mid);border:2px solid #2c1816;display:flex;align-items:center;justify-content:center}
.ct{position:absolute;color:var(--white);font-size:14px;line-height:1.5}
.news-field{position:absolute;left:355px;top:420px;width:490px;height:54px;border:2px solid #cfe8b8;border-radius:28px;padding:17px 0 0 30px;font-size:13px;color:#dff0cf}
.news-btn{position:absolute;left:700px;top:420px;width:145px;height:54px;border-radius:28px;background:var(--cocoa-mid);color:var(--white);font-size:20px;text-align:center;line-height:54px}
.tips{position:absolute;left:0;top:540px;width:1200px;text-align:center;font-size:15px;color:var(--white)}
.social{position:absolute;top:582px;width:58px;height:58px;border-radius:50%;background:var(--cocoa-mid);border:2px solid #2c1816}
.copy{position:absolute;left:0;top:672px;width:1200px;text-align:center;font-size:14px;color:var(--white)}
.copy b{font-weight:400}
.top-btn{position:absolute;left:1058px;top:3278px;width:90px;height:34px;border-radius:50%;background:var(--cocoa)}
</style>
</head>
<body>

<!-- HERO -->
<section class="hero">
  <div class="photo" role="img" aria-label="Melted chocolate dripping down from the top edge" style="left:0;top:0;width:1200px;height:200px;border-radius:0;background:linear-gradient(180deg,var(--cocoa) 0%,var(--cocoa) 45%,rgba(59,35,32,0) 100%)"></div>
  <nav class="nav">
    <a class="current" style="left:124px">Home</a>
    <a style="left:228px">About</a>
    <a style="left:334px">Product</a>
    <a style="left:810px">Contact Us</a>
  </nav>
  <div class="cart-pill">3 Products
    <div class="cart-dot">
      <svg width="54" height="32" viewBox="0 0 54 32" aria-hidden="true"><path d="M17 10h4l3 11h10l3-8H23" fill="none" stroke="#1c2a05" stroke-width="2.2" stroke-linejoin="round"/><circle cx="25" cy="25" r="2" fill="#1c2a05"/><circle cx="33" cy="25" r="2" fill="#1c2a05"/></svg>
    </div>
  </div>
  <div class="brand">
    <div class="brand-mark"></div>
    <div class="brand-name">Brimora</div>
  </div>
  <div class="photo" role="img" aria-label="Nuttaree cup with chocolate pieces, coconut and cocoa curls" style="left:50px;top:285px;width:545px;height:360px;border-radius:40px;background:linear-gradient(120deg,#5a3a2a 0%,#e9e1cc 30%,#a88a5a 55%,#6d4128 80%,#f0ece2 100%)"></div>
  <h1 class="hero-title script">Nuttaree</h1>
  <p class="hero-tag">"Fuel for the Bold Trail-Walker(tm)."</p>
  <a class="btn-shop">Shop Now</a>
</section>

<!-- WELCOME -->
<section>
  <div class="photo" role="img" aria-label="Stack of dark chocolate bars with nuts" style="left:40px;top:728px;width:200px;height:140px;background:linear-gradient(135deg,#6b4634,#2f1c15)"></div>
  <div class="watermark-ring"></div>
  <h2 class="welcome-title script">welcome to <span>Brimora</span></h2>
  <div class="welcome-text">
    <p>Our products are raw, organic, vegan, gluten-free, dairy-free, fiber-rich, nutrient-dense, antioxidant-rich real foods with no preservatives, no added sugar, and no artificial or plant-based sweeteners.</p>
    <p>And they are irresistibly scrumptious!</p>
  </div>
  <div class="photo" role="img" aria-label="Scoops of pink, green and chocolate ice cream on a waffle cone" style="left:965px;top:955px;width:235px;height:185px;border-radius:90px 0 0 90px;background:linear-gradient(120deg,#f2a8c0,#cfe6b8 40%,#6a3e28 65%,#e2b070)"></div>
  <div class="divider"></div>
  <div class="divider-dot"></div>
</section>

<!-- TOP PRODUCTS -->
<section>
  <div class="card feature" style="left:77px;top:1272px">
    <h3 class="script">top <span>product</span></h3>
    <p>Lorem Ipsum is simply dummy text of the printing and typesetting industry. Lorem Ipsum has been the industry's standard dummy text ever since the 1500s, when an unknown printer took a galley of type and scrambled it to make a type specimen book.</p>
  </div>
  <div class="card" style="left:343px;top:1272px">
    <div class="card-name">Lorem ipsum text.</div>
    <div class="photo" role="img" aria-label="Square raw chocolate brownie" style="left:50px;top:110px;width:150px;height:150px;background:linear-gradient(135deg,#d8cfcc,#b9aaa6)"></div>
    <div class="tools">
      <div class="tool"><svg width="20" height="20" viewBox="0 0 20 20" aria-hidden="true"><path d="M10 17S3 12 3 7.5A3.5 3.5 0 0 1 10 6a3.5 3.5 0 0 1 7 1.5C17 12 10 17 10 17Z" fill="#3a3a3a"/></svg></div>
      <div class="tool"><svg width="20" height="20" viewBox="0 0 20 20" aria-hidden="true"><path d="M2 4h3l2 9h8l2-6H6" fill="none" stroke="#3a3a3a" stroke-width="1.8"/><circle cx="8" cy="16" r="1.4" fill="#3a3a3a"/><circle cx="14" cy="16" r="1.4" fill="#3a3a3a"/></svg></div>
      <div class="tool"><svg width="20" height="20" viewBox="0 0 20 20" aria-hidden="true"><path d="M3 7h13l-3-3M17 13H4l3 3" fill="none" stroke="#3a3a3a" stroke-width="1.8"/></svg></div>
    </div>
    <div class="card-price">Our Price: <b>$250</b></div>
  </div>
  <div class="card" style="left:608px;top:1272px">
    <div class="card-name">Lorem ipsum Dummy text.</div>
    <div class="photo" role="img" aria-label="Chocolate cupcake with frosting" style="left:60px;top:110px;width:130px;height:150px;background:linear-gradient(180deg,#5a2f22,#2e1812)"></div>
    <div class="card-price">Our Price: <b>$395</b></div>
  </div>
  <div class="card" style="left:872px;top:1272px">
    <div class="card-name">Lorem ipsum text.</div>
    <div class="photo" role="img" aria-label="Soft-serve dessert in a bowl with raspberries" style="left:45px;top:100px;width:160px;height:160px;background:linear-gradient(180deg,#f4f2ee 55%,#d23a4a)"></div>
    <div class="card-price">Our Price: <b>$980</b></div>
  </div>
</section>

<!-- TESTIMONIAL -->
<section class="testimonial">
  <h2 class="script">testimonial</h2>
  <span class="quote" style="left:150px;top:130px">&ldquo;</span>
  <p>Lorem Ipsum is simply dummy text of the printing and typesetting industry. Lorem Ipsum has been the industry's standard dummy text ever since the 1500s, when an unknown printer took a galley of type and scrambled it to make a type specimen book.</p>
  <div class="who script">Lorem ipsum</div>
  <span class="quote" style="left:1005px;top:250px">&rdquo;</span>
</section>

<!-- NEW PRODUCTS -->
<section>
  <div class="photo" role="img" aria-label="Rolled wafer sticks" style="left:0;top:2080px;width:110px;height:170px;border-radius:0;background:linear-gradient(160deg,#c79a5c,#6b3e22)"></div>
  <div class="card" style="left:77px;top:2130px">
    <div class="photo" role="img" aria-label="Nuttaree cup with chocolate pieces" style="left:18px;top:30px;width:215px;height:210px;background:linear-gradient(180deg,#ece6d6 40%,#7a3f22)"></div>
    <div class="card-name low">Lorem ipsum text.</div>
    <div class="card-note">Lorem Ipsum is simply dummy text of the printing...</div>
  </div>
  <div class="card" style="left:343px;top:2130px">
    <div class="photo" role="img" aria-label="Round Nuttaree package lid" style="left:28px;top:20px;width:195px;height:195px;border-radius:50%;background:radial-gradient(circle,#cfb58a,#8a6a44)"></div>
    <div class="card-name low">Lorem ipsum text.</div>
    <div class="card-note">Lorem Ipsum is simply dummy text of the printing...</div>
  </div>
  <div class="card" style="left:608px;top:2130px">
    <div class="photo" role="img" aria-label="Nuttaree cup with orange slice" style="left:18px;top:30px;width:215px;height:210px;background:linear-gradient(180deg,#ece6d6 40%,#6d3a22 75%,#f09a2a)"></div>
    <div class="card-name low">Lorem ipsum Dummy text.</div>
    <div class="card-note">Lorem Ipsum is simply dummy text of the printing...</div>
  </div>
  <div class="card feature" style="left:872px;top:2130px">
    <h3 class="script">new <span>product</span></h3>
    <p>Lorem Ipsum is simply dummy text of the printing and typesetting industry. Lorem Ipsum has been the industry's standard dummy text ever since the 1500s, when an unknown printer took a galley of type and scrambled it to make a type specimen book.</p>
  </div>
</section>

<!-- CONTACT -->
<footer class="contact">
  <div class="photo" role="img" aria-label="Blurred cupcake tops in green" style="left:0;top:0;width:1200px;height:727px;border-radius:0;background:radial-gradient(circle at 10% 30%,rgba(140,190,60,.35),transparent 25%),radial-gradient(circle at 90% 85%,rgba(140,190,60,.3),transparent 25%)"></div>
  <div class="photo" role="img" aria-label="Melted chocolate dripping over a chocolate-dipped strawberry" style="left:830px;top:0;width:370px;height:330px;border-radius:0 0 0 60px;background:linear-gradient(180deg,rgba(59,35,32,.95) 0%,rgba(59,35,32,.8) 55%,rgba(120,40,40,.5) 85%,rgba(59,35,32,0) 100%)"></div>

  <h2 class="script" style="top:85px">contact us</h2>
  <p class="lead">Want to talk to a Customer Specialist? Give Us a CALL to Book your Appointment</p>

  <div class="ci" style="left:208px"><svg width="22" height="26" viewBox="0 0 22 26" aria-hidden="true"><path d="M11 24S3 14 3 9a8 8 0 0 1 16 0c0 5-8 15-8 15Z" fill="none" stroke="#fff" stroke-width="2"/><circle cx="11" cy="9" r="3" fill="#fff"/></svg></div>
  <div class="ct" style="left:280px;top:236px">123 Lorem ipsum dummy text,<br>Country 123456.</div>

  <div class="ci" style="left:512px"><svg width="24" height="24" viewBox="0 0 24 24" aria-hidden="true"><path d="M5 3h4l2 5-3 2a12 12 0 0 0 6 6l2-3 5 2v4c0 1-1 2-2 2A18 18 0 0 1 3 5c0-1 1-2 2-2Z" fill="none" stroke="#fff" stroke-width="1.8"/></svg></div>
  <div class="ct" style="left:588px;top:244px;font-size:18px">123 555 0192</div>

  <div class="ci" style="left:758px"><svg width="26" height="20" viewBox="0 0 26 20" aria-hidden="true"><rect x="2" y="2" width="22" height="16" fill="none" stroke="#fff" stroke-width="1.8"/><path d="M2 3l11 9 11-9" fill="none" stroke="#fff" stroke-width="1.8"/></svg></div>
  <div class="ct" style="left:832px;top:247px">hello@brimorafoods.com</div>

  <h2 class="script" style="top:345px">newsletter</h2>
  <div class="news-field">Enter Your E-Mail</div>
  <div class="news-btn script">Subscribe</div>

  <p class="tips">Get helpful beauty tips and specials offers</p>
  <div class="social" style="left:536px"></div>
  <div class="social" style="left:606px"></div>

  <p class="copy">&copy;<b>Brimora</b> - 2018. All Rights reserved.</p>
</footer>
<div class="top-btn"></div>

</body>
</html>
```